Ostrivane Capital LLC

Need Professional Business cards for New Investment Fund

Target Market(s)

High Quality investors

Industry/Entity Type

Financial

Contact Information for Business Card

Phone Number +1 555 284 6190
Name Lukas Varenko
Title Fund Manager
email lv@FundOstrivane.com
Website www.FundOstrivane.com

Colors

Designer to choose colors to be used in the design.

Requirements
Must have
• Must have our Logo and all of the above. Must be made so lettering and loge can be raised

```html
<!DOCTYPE html>
<html lang="en">
<head>
<meta charset="utf-8">
<title>Ostrivane Capital – Business Card</title>
<link href="https://fonts.googleapis.com/css2?family=Mulish:wght@700&family=Questrial&display=swap" rel="stylesheet">
<style>
  :root {
    --backdrop: #2b2b2b;
    --card: #1e1e1e;
    --green: #5cb947;
    --green-dark: #3d4d3c;
    --white: #ffffff;
    --rule: #5a5a5a;
  }
  * { box-sizing: border-box; margin: 0; padding: 0; }
  html, body {
    width: 1200px; height: 895px; overflow: hidden;
    background: var(--backdrop);
  }
  .stage { position: relative; width: 1200px; height: 895px; }
  .card {
    position: absolute; top: 157px;
    width: 331px; height: 581px;
    border-radius: 12px;
    background: var(--card);
    border-bottom: 3px solid var(--green);
    border-right: 2px solid var(--green);
    overflow: hidden;
  }
  .card--front { left: 241px; }
  .card--back { left: 631px; }

  .brand {
    position: absolute; top: 178px; left: 0; right: 0;
    text-align: center;
    font-family: "Mulish", sans-serif; font-weight: 700;
    font-size: 34px; letter-spacing: 2px;
    color: var(--white);
  }

  .holder {
    position: absolute; top: 394px; left: 0; right: 0;
    text-align: center;
  }
  .holder__name {
    font-family: "Mulish", sans-serif; font-weight: 700;
    font-size: 24px; letter-spacing: 0.6px;
    color: var(--green); text-transform: uppercase; line-height: 28px;
  }
  .holder__title {
    font-family: "Questrial", sans-serif;
    font-size: 17px; letter-spacing: 1.1px;
    color: var(--white); line-height: 20px;
  }

  .icon-row {
    position: absolute; top: 449px; left: 0; right: 0;
    display: flex; align-items: center; justify-content: center; gap: 3px;
  }
  .icon-row__rule { width: 45px; height: 1px; background: var(--rule); margin: 0 3px; }
  .icon-row__icon {
    width: 21px; height: 21px; border-radius: 50%;
    background: var(--green);
    display: flex; align-items: center; justify-content: center;
  }

  .contact {
    position: absolute; top: 475px; left: 0; right: 0;
    text-align: center;
    font-family: "Questrial", sans-serif;
    font-size: 16.5px; letter-spacing: 1.3px; line-height: 19.5px;
    color: var(--white);
  }

  .pattern-area {
    position: absolute; inset: 0;
    background: linear-gradient(90deg, var(--green) 0 12%, var(--card) 12% 25%, var(--green-dark) 25% 33%, var(--card) 33% 45%, var(--green) 45% 57%, var(--card) 57% 70%, var(--green-dark) 70% 78%, var(--card) 78% 88%, var(--green) 88% 100%);
    opacity: 0.55;
  }
</style>
</head>
<body>
<main class="stage">
  <section class="card card--front">
    <div class="brand">OSTRIVANE</div>

    <div class="holder">
      <p class="holder__name">Lukas Varenko</p>
      <p class="holder__title">Fund Manager</p>
    </div>

    <div class="icon-row">
      <span class="icon-row__rule"></span>
      <span class="icon-row__icon" aria-label="Phone">
        <svg width="12" height="10" viewBox="0 0 12 10"><path d="M1 3 Q6 0 11 3 L10 4.5 L8 4 L8 3 Q6 2.4 4 3 L4 4 L2 4.5 Z M3 5 H9 L10 9 H2 Z" fill="#fff"/></svg>
      </span>
      <span class="icon-row__icon" aria-label="Email">
        <svg width="12" height="9" viewBox="0 0 12 9"><rect x="0.5" y="0.5" width="11" height="8" rx="1" fill="#fff"/><path d="M1 1.5 L6 5 L11 1.5" stroke="#5cb947" stroke-width="1.2" fill="none"/></svg>
      </span>
      <span class="icon-row__icon" aria-label="Website">
        <svg width="13" height="13" viewBox="0 0 13 13" fill="none" stroke="#fff" stroke-width="1"><circle cx="6.5" cy="6.5" r="5.5"/><ellipse cx="6.5" cy="6.5" rx="2.5" ry="5.5"/><path d="M1 6.5 H12 M2 3.8 H11 M2 9.2 H11"/></svg>
      </span>
      <span class="icon-row__rule"></span>
    </div>

    <div class="contact">
      <p>+1 555 284 6190</p>
      <p>lv@FundOstrivane.com</p>
      <p>www.FundOstrivane.com</p>
    </div>
  </section>

  <section class="card card--back">
    <div class="pattern-area" role="img" aria-label="Repeating brand pattern in bright and muted green stripes"></div>
  </section>
</main>
</body>
</html>
```